Driver License Monitoring Application Marketing Website

We need a new web design for our web application. The product is called "RoadPermitGuard." We provide a driver license monitoring service to companies and local government bodies with driver fleets. Our current website is available at www.RoadPermitGuard-example.com.

I prefer a clean, single-page design with good SEO. Attached are some PDFs with data about the project.

Target Market(s)

Companies with driver fleets, local government.

Industry/Entity Type

Government

Coding

Coded - Design and coding required

Number of Pages Required

1 page

Colors
000000

Requirements
Must have
• Content from current www.RoadPermitGuard-example.com and attached PDFs.
Nice to have
• Prefer a simple Bootstrap or similar design for easy editing.
• Room for a simple video explanation of how the product works (we don't have an actual video yet)

```html
<!DOCTYPE html>
<html lang="en">
<head>
<meta charset="utf-8">
<title>RoadPermitGuard – Florida Driver License Monitoring</title>
<link href="https://fonts.googleapis.com/css2?family=Open+Sans:ital,wght@0,400;0,600;1,400&family=Tinos:wght@400;700&display=swap" rel="stylesheet">
<style>
:root{
  --red:#c0393b;
  --red-soft:#d3585a;
  --red-light:#e36b6d;
  --dark:#1d1d1b;
  --dark-band:#22221f;
  --footer:#2b2b28;
  --ink:#333;
  --muted:#888;
  --light-bg:#f4f3f3;
  --white:#fff;
}
*{margin:0;padding:0;box-sizing:border-box}
html,body{width:952px;height:1200px;overflow:hidden}
body{font-family:"Open Sans",sans-serif;color:var(--ink);background:var(--white);position:relative}
.abs{position:absolute}

/* header */
.site-header{left:0;top:0;width:952px;height:72px;background:var(--white);border-top:2px solid var(--red)}
.brand{left:78px;top:24px;font-family:"Tinos",serif;font-weight:700;font-size:21px;color:#1a1a1a;letter-spacing:.3px}
.brand .mark{display:inline-block;width:10px;height:10px;background:var(--red);margin-right:6px;vertical-align:2px}
.nav a{position:absolute;top:0;height:50px;line-height:52px;font-size:9px;color:#444;text-decoration:none;letter-spacing:.2px}
.nav a.active{background:var(--red-soft);color:var(--white);padding:0 12px}
.search{left:864px;top:30px}

/* hero */
.hero-band{left:0;top:72px;width:952px;height:342px;background:var(--dark)}
.slider{left:78px;top:95px;width:796px;height:290px;background:linear-gradient(100deg,#6c6c6c 0%,#bdbdbd 25%,#e8e8e8 50%,#d6d6d6 70%,#8f8f8f 100%);box-shadow:0 2px 6px rgba(0,0,0,.6)}
.slide-copy{left:468px;top:155px;width:380px;text-align:center}
.slide-title{font-family:"Tinos",serif;font-weight:700;font-size:24px;line-height:30px;color:var(--red-soft);letter-spacing:.5px;white-space:nowrap}
.slide-sub{font-size:20px;line-height:26px;color:#555;margin-top:0;letter-spacing:.5px}
.slide-text{font-size:9px;color:#333;line-height:16px;margin:10px auto 0;width:310px}
.btn{display:inline-block;background:var(--red);color:var(--white);font-size:9px;padding:7px 11px;margin-top:9px}
.arrow{width:22px;height:28px;background:rgba(0,0,0,.55)}

/* about */
.about{left:0;top:414px;width:952px;height:160px;background:var(--dark-band);text-align:center;color:var(--white);border-top:3px solid #151513}
.about h2{font-family:"Tinos",serif;font-weight:400;font-size:21px;margin-top:19px;letter-spacing:.5px}
.about .lead{font-style:italic;font-size:11px;margin-top:13px}
.about .tag{font-size:9px;color:var(--red-light);margin-top:4px}
.about p.body{font-size:9px;line-height:16px;width:720px;margin:1px auto 0}
.about .more{font-style:italic;font-size:10px;color:var(--red-light);margin-top:6px}

/* industries */
.industries-title{left:0;top:612px;width:952px;text-align:center;font-family:"Tinos",serif;font-weight:400;font-size:21px;color:#555}
.card{top:666px;width:189px;height:224px;border:1px solid #e6e6e6;background:var(--white);text-align:center;box-shadow:0 6px 4px -4px rgba(0,0,0,.25)}
.card .photo{margin:4px auto 0;width:179px;height:126px}
.card h3{font-size:11px;font-weight:600;color:#444;margin-top:15px}
.card p{font-size:8px;line-height:14px;color:var(--muted);margin-top:4px;padding:0 12px}
.pill{display:inline-block;background:var(--red);color:var(--white);font-size:8px;padding:3px 7px;border-radius:9px;margin-top:7px}

/* sectors */
.sectors{left:0;top:936px;width:952px;height:158px;background:var(--light-bg)}
.sector-icon{width:66px;height:66px;border-radius:50%;background:var(--white);border:2px solid #ececec;display:flex;align-items:center;justify-content:center}
.sector-box{width:285px;height:81px;background:var(--white);border:2px solid #ececec;padding:10px 20px}
.sector-box h4{font-size:12px;font-weight:600;color:#444}
.sector-box h4 span{font-size:9px;font-weight:400;color:var(--red-light);margin-left:4px}
.sector-box p{font-size:8px;line-height:14px;color:var(--muted);margin-top:5px}
.sector-box .read{font-style:italic;font-size:9px;color:var(--red-light);text-align:right;margin-top:3px}

/* footer */
.site-footer{left:0;top:1094px;width:952px;height:106px;background:var(--footer)}
.foot-links{left:78px;top:18px;font-size:8.5px;color:#aaa;word-spacing:2px}
.copy{left:78px;top:41px;font-size:8.5px;color:#aaa}
.signup{left:654px;top:21px;width:220px;height:26px;background:#353532;font-size:9px;color:#aaa;line-height:26px;padding-left:9px}
.signup .go{position:absolute;right:0;top:0;width:37px;height:26px;background:var(--red-soft);color:var(--white);text-align:center;font-size:8.5px}
.social{top:66px;width:22px;height:22px;border-radius:50%;background:#3a3a37}
</style>
</head>
<body>

<header class="site-header abs">
  <div class="brand abs"><span class="mark"></span>RoadPermitGuard</div>
  <nav class="nav">
    <a class="active" style="left:411px">HOME</a>
    <a style="left:485px">LICENSE MONITORING</a>
    <a style="left:615px">ABOUT US</a>
    <a style="left:695px">CONTACT</a>
    <a style="left:772px">CLIENT LOGIN</a>
  </nav>
  <svg class="search abs" width="9" height="9" viewBox="0 0 10 10"><circle cx="4" cy="4" r="3" fill="none" stroke="#777" stroke-width="1.5"/><line x1="6.3" y1="6.3" x2="9" y2="9" stroke="#777" stroke-width="1.5"/></svg>
</header>

<section class="hero-band abs"></section>
<div class="slider abs" role="img" aria-label="Photo of a white delivery truck in motion"></div>
<div class="arrow abs" style="left:78px;top:226px"><svg width="22" height="28"><polyline points="13,9 8,14 13,19" fill="none" stroke="#fff" stroke-width="1.5"/></svg></div>
<div class="arrow abs" style="left:852px;top:226px"><svg width="22" height="28"><polyline points="9,9 14,14 9,19" fill="none" stroke="#fff" stroke-width="1.5"/></svg></div>
<div class="slide-copy abs">
  <div class="slide-title">FLORIDA DRIVER LICENSE</div>
  <div class="slide-sub">MONITORING</div>
  <div class="slide-text">Monitor your fleet electronically. Get alerts by email and online. Never let another unlicensed or unauthorized driver behind the wheel.</div>
  <span class="btn">VIEW MORE</span>
</div>

<section class="about abs">
  <h2>ABOUT US</h2>
  <div class="lead">Created by experts in Florida traffic law</div>
  <div class="tag">Dedicated to Advancing Safety, Performance, and Economy</div>
  <p class="body">RoadPermitGuard was created by legal professionals to help organizations improve safety and performance. It was conceived by Daniel R. Marsh, Esq. A native Floridian, Daniel Marsh is a lawyer who has practiced in traffic and driver license law since 2007. Before law school, Mr. Marsh obtained a Bachelor's Degree.......</p>
  <div class="more">More »</div>
</section>

<h2 class="industries-title abs">INDUSTRIES</h2>

<div class="card abs" style="left:78px">
  <div class="photo" role="img" aria-label="Photo of a red semi truck on a highway" style="background:linear-gradient(#7b8a99,#5d5450 55%,#3d3b38)"></div>
  <h3>COMMERCIAL SECTOR</h3>
  <p>Lorem ipsum dolor sit amet, tur scing elit, sed do eiusmod veniam,</p>
  <span class="pill">View More</span>
</div>
<div class="card abs" style="left:280px">
  <div class="photo" role="img" aria-label="Photo of a yellow school bus front" style="background:linear-gradient(135deg,#2f6fa8,#e3a322 45%,#f2b52a)"></div>
  <h3>SCHOOL DISTRICTS</h3>
  <p>Lorem ipsum dolor sit amet, tur scing elit, sed do eiusmod veniam,</p>
  <span class="pill">View More</span>
</div>
<div class="card abs" style="left:482px">
  <div class="photo" role="img" aria-label="Image of a state flag with seal" style="background:linear-gradient(135deg,#d94040,#f3f0ea 40%,#e8d04a 60%,#d94040)"></div>
  <h3>GOVERNMENT</h3>
  <p>Lorem ipsum dolor sit amet, tur scing elit, sed do eiusmod veniam,</p>
  <span class="pill">View More</span>
</div>
<div class="card abs" style="left:684px">
  <div class="photo" role="img" aria-label="Photo of hands reviewing charts on a tablet" style="background:linear-gradient(135deg,#2b3442,#dfe4ea 45%,#f3f5f8 70%,#3a87cf)"></div>
  <h3>INSURANCE INDUSTRY</h3>
  <p>Lorem ipsum dolor sit amet, tur scing elit, sed do eiusmod veniam,</p>
  <span class="pill">View More</span>
</div>

<section class="sectors abs">
  <div class="sector-icon abs" style="left:78px;top:46px">
    <svg width="22" height="24" viewBox="0 0 22 24"><rect x="2" y="2" width="18" height="17" rx="4" fill="none" stroke="#e36b6d" stroke-width="2"/><line x1="2" y1="11" x2="20" y2="11" stroke="#e36b6d" stroke-width="2"/><circle cx="6" cy="15" r="1.4" fill="#e36b6d"/><circle cx="16" cy="15" r="1.4" fill="#e36b6d"/><line x1="5" y1="19" x2="5" y2="22" stroke="#e36b6d" stroke-width="2"/><line x1="17" y1="19" x2="17" y2="22" stroke="#e36b6d" stroke-width="2"/></svg>
  </div>
  <div class="sector-box abs" style="left:163px;top:40px">
    <h4>COMMERCIAL<span>Private Sector</span></h4>
    <p>The private sector is fraught with risk. Having an unlicensed or ized driver take the wheel can be disastrous....</p>
    <div class="read">Read More ⊕</div>
  </div>
  <div class="sector-icon abs" style="left:504px;top:46px">
    <svg width="24" height="22" viewBox="0 0 24 22"><line x1="3" y1="2" x2="3" y2="21" stroke="#e36b6d" stroke-width="2"/><path d="M3 3 Q8 1 12 4 T21 4 V13 Q16 15 12 12 T3 12Z" fill="none" stroke="#e36b6d" stroke-width="1.8"/><line x1="3" y1="7.5" x2="21" y2="8.5" stroke="#e36b6d" stroke-width="1.2"/></svg>
  </div>
  <div class="sector-box abs" style="left:588px;top:40px">
    <h4>GOVERNMENT<span>Public Sector</span></h4>
    <p>The private sector is fraught with risk. Having an unlicensed or ized driver take the wheel can be disastrous....</p>
    <div class="read">Read More ⊕</div>
  </div>
</section>

<footer class="site-footer abs">
  <div class="foot-links abs">Home / License Monitoring / About Us / Contact / Client Login</div>
  <div class="copy abs">Copyrights@roadpermitguard.2015. &nbsp;Allrights Reserved</div>
  <div class="signup abs">Signup With your email<span class="go">GO !</span></div>
  <span class="social abs" style="left:772px"></span>
  <span class="social abs" style="left:799px"></span>
  <span class="social abs" style="left:826px"></span>
  <span class="social abs" style="left:852px"></span>
</footer>

</body>
</html>
```